Kelvor Engineers: Why you should hire us keepsake

New design. Open to plastic cards. We are an engineering firm that designs cell phone towers and commercial buildings. Please check out our website www.kelvorstruct.com for more details. We want people to remember our card and for it to be useful if possible. We want the same look and feel on these cards to be translated to other marketing material we may need such as brochures.

Target Market(s)

Architects, Developers and Telecommunication Carriers

Industry/Entity Type

Engineering

Contact Information for Business Card

Card with our company colors, logo, and innovative design with elements related to our industry.

Font styles to use
Sans Serif

Colors
9bcb3c
abd036
0255a3

Requirements
Must have
• Sleek and hip design
Nice to have
• Bright lime green and navy coloring that pops with an innovative design.
Should not have
• A basic and boring design

```html
<!DOCTYPE html>
<html lang="en">
<head>
<meta charset="utf-8">
<title>Kelvor Engineers — Business Card</title>
<link href="https://fonts.googleapis.com/css2?family=Roboto:wght@400;500;700;900&family=Roboto+Condensed:wght@500;700&display=swap" rel="stylesheet">
<style>
  :root {
    --backdrop: #2b2b2b;
    --paper: #f1f1f1;
    --lime: #1fe81c;
    --navy: #042a5a;
    --ink-light: #eef2f7;
    --ink-grey: #4a4a4a;
  }
  * { margin: 0; padding: 0; box-sizing: border-box; }
  html, body { width: 1200px; height: 960px; overflow: hidden; }
  body {
    background: var(--backdrop);
    position: relative;
    font-family: "Roboto", Arial, sans-serif;
  }
  .card {
    position: absolute;
    width: 600px;
    height: 343px;
    background: var(--paper);
    box-shadow: 0 2px 6px rgba(0,0,0,0.5);
    overflow: hidden;
  }
  .card--front { left: 314px; top: 113px; }
  .card--back { left: 311px; top: 472px; }

  .wordmark {
    position: absolute;
    color: var(--lime);
    font-family: "Roboto", Arial, sans-serif;
    font-weight: 900;
    letter-spacing: -1px;
    line-height: 1;
    white-space: nowrap;
  }
  .card--front .wordmark {
    left: 0; width: 294px; top: 138px;
    text-align: center;
    font-size: 66px;
  }
  .divider {
    position: absolute;
    left: 294px; top: 0;
    width: 6px; height: 100%;
    background: var(--lime);
  }
  .contact-panel {
    position: absolute;
    left: 300px; top: 0;
    width: 300px; height: 100%;
    background: var(--navy);
  }
  .pointer {
    position: absolute;
    left: 300px; top: 60px;
    width: 0; height: 0;
    border-top: 14px solid transparent;
    border-bottom: 14px solid transparent;
    border-left: 21px solid var(--lime);
  }
  .person-name {
    position: absolute;
    left: 343px; top: 62px;
    color: var(--lime);
    font-family: "Roboto Condensed", "Roboto", sans-serif;
    font-weight: 500;
    font-size: 20px;
    letter-spacing: 0.2px;
  }
  .contact-list {
    position: absolute;
    left: 345px; top: 205px;
    list-style: none;
  }
  .contact-list li {
    display: flex;
    align-items: center;
    height: 19px;
    color: var(--ink-light);
    font-size: 14.5px;
  }
  .contact-list svg {
    width: 12px; height: 12px;
    margin-right: 10px;
    fill: var(--lime);
    flex: none;
  }

  .card--back .wordmark {
    left: 0; width: 100%; top: 122px;
    text-align: center;
    font-size: 92px;
  }
  .tagline {
    position: absolute;
    left: 0; width: 100%; top: 265px;
    display: flex; justify-content: center; align-items: center;
    color: var(--lime);
    font-weight: 700;
    font-size: 16px;
  }
  .tagline::before, .tagline::after {
    content: "";
    width: 30px; height: 2px;
    background: var(--navy);
    margin: 0 2px;
  }
  .locations {
    position: absolute;
    left: 0; width: 100%; top: 288px;
    text-align: center;
    color: var(--ink-grey);
    font-size: 15.5px;
    letter-spacing: 0.8px;
  }
</style>
</head>
<body>
  <section class="card card--front">
    <div class="wordmark">Kelvor</div>
    <div class="divider"></div>
    <div class="contact-panel"></div>
    <div class="pointer"></div>
    <h1 class="person-name">DANA WELLS HARMON</h1>
    <ul class="contact-list">
      <li>
        <svg viewBox="0 0 12 12" aria-hidden="true"><path d="M2.4 0.5 L4.3 2.8 L3.2 4.2 C3.9 5.8 5.6 7.6 7.8 8.8 L9.2 7.7 L11.5 9.6 L10.4 11.4 C5.5 11 1 6.5 0.6 1.6 Z"/></svg>
        555.014.2290
      </li>
      <li>
        <svg viewBox="0 0 12 12" aria-hidden="true"><path d="M3 0 H9 A1 1 0 0 1 10 1 V11 A1 1 0 0 1 9 12 H3 A1 1 0 0 1 2 11 V1 A1 1 0 0 1 3 0 Z M3.5 1.5 V9.5 H8.5 V1.5 Z M5.3 10.2 H6.7 V11.2 H5.3 Z"/></svg>
        555.017.3346
      </li>
      <li>
        <svg viewBox="0 0 12 12" aria-hidden="true"><path d="M0.5 2.5 H11.5 V3.2 L6 7 L0.5 3.2 Z M0.5 4.4 L6 8.2 L11.5 4.4 V9.5 H0.5 Z"/></svg>
        dharmon@kelvorstruct.com
      </li>
      <li>
        <svg viewBox="0 0 12 12" aria-hidden="true"><circle cx="6" cy="6" r="5.5"/><path d="M3 3 L5 3.5 L5.5 5.5 L4 6.5 L3.5 9 L2 6 Z M7 2 L9.5 3.5 L9 5 L7.5 4.5 Z M7 7 L9.5 7.5 L8 10 L6.5 9.5 Z" fill="#042a5a"/></svg>
        www.kelvorstruct.com
      </li>
    </ul>
  </section>

  <section class="card card--back">
    <div class="wordmark">Kelvor</div>
    <p class="tagline">MULTI-DISCIPLINE ENGINEERING</p>
    <p class="locations">Denver | Nashville | Phoenix | Kansas City</p>
  </section>
</body>
</html>
```